New business card for a regional office of a US M&A company

We need business card for a finance company, office based in Hong Kong , our Head office is in US, our business is to Merge and acquires companies , the new office will be a regional office for the Asia Pacific region. We want to use the head office logo as attached ( but don't have to be exactly the same, can be a variation to it) as a base and then add Asia Pacific alongside the logo.
We would prefer to have be bilingual Eng + Chinese, although we don't really have Chinese company name .

Industry/Entity Type

Business

Contact Information for Business Card

Clara Jo Tsang
 

VP,
APAC M&A Operations
ORIN VANTAGE ASIA PACIFIC Limited
 
Unit 1407, K18
18 Tai Lok Shan Road, 
Hong Kong 
 
M: +852 6038 1742
T : +852 2836 4100
F : +852 2836 4177
VOIP: 4158
 
cjtsang@orinvantage.com

Font styles to use
Serif
Sans Serif

Colors

Designer to choose colors to be used in the design.

Requirements
Must have
• APAC Office

```html
<!DOCTYPE html>
<html lang="en">
<head>
<meta charset="utf-8">
<title>Orin Vantage Asia Pacific – Business Card</title>
<link rel="stylesheet" href="https://fonts.googleapis.com/css2?family=Source+Sans+3:wght@400;600;700&display=swap">
<style>
  :root {
    --backdrop: #808080;
    --card-navy: #0d2742;
    --card-navy-deep: #0a2139;
    --ink-light: #ffffff;
    --ink-soft: #e3e8ee;
  }
  html, body {
    margin: 0;
    width: 1200px;
    height: 900px;
    overflow: hidden;
    background: var(--backdrop);
    font-family: "Source Sans 3", "Myriad Pro", Arial, sans-serif;
  }
  .stage { position: relative; width: 1200px; height: 900px; }

  .card {
    position: absolute;
    top: 200px;
    width: 310px;
    height: 502px;
    background: var(--card-navy);
    color: var(--ink-light);
    overflow: hidden;
  }
  .card--front { left: 265px; border-radius: 62px 0 62px 0; }
  .card--back  { left: 641px; width: 309px; border-radius: 0 62px 0 62px; background: var(--card-navy-deep); }

  .brand-mark {
    position: absolute;
    left: 147px; top: 70px;
    width: 54px; height: 54px;
    background: var(--ink-light);
  }
  .brand-name {
    position: absolute;
    left: 0; right: 0; top: 166px;
    text-align: center;
    padding-left: 24px;
    font-weight: 700;
    font-size: 16.5px;
    letter-spacing: 0.1px;
    margin: 0;
  }

  .person { position: absolute; left: 15px; top: 221px; margin: 0; }
  .person__name { font-weight: 600; font-size: 18.5px; line-height: 24px; margin: 0; }
  .person__role { font-size: 14px; line-height: 18px; color: var(--ink-soft); margin: 0; }

  .office { position: absolute; left: 15px; top: 286px; font-style: normal; }
  .office__company { font-weight: 600; font-size: 16px; line-height: 22px; margin: 0; }
  .office__address { font-size: 14.5px; line-height: 21px; color: var(--ink-soft); margin: 0; }

  .contacts {
    position: absolute; left: 17px; top: 368px;
    list-style: none; margin: 0; padding: 0;
    font-size: 14px; line-height: 21px; color: var(--ink-soft);
  }
  .contacts li { display: flex; align-items: center; height: 21px; }
  .contacts svg { width: 11px; height: 11px; margin-right: 9px; fill: var(--ink-soft); }

  .back-field {
    position: absolute; inset: 0;
    background: linear-gradient(180deg, #0b2440 0%, #0c2742 50%, #0a2139 100%);
  }
  .back-name {
    position: absolute; left: 0; right: 0; top: 437px;
    text-align: center; margin: 0;
    font-weight: 700; font-size: 19.5px; letter-spacing: 0.2px;
  }
</style>
</head>
<body>
<main class="stage">
  <section class="card card--front">
    <div class="brand-mark"></div>
    <p class="brand-name">ORIN VANTAGE ASIA PACIFIC</p>

    <div class="person">
      <p class="person__name">Clara Jo Tsang VP,</p>
      <p class="person__role">APAC M&amp;A Operations</p>
    </div>

    <address class="office">
      <p class="office__company">Orin Vantage Asia Pacific Ltd</p>
      <p class="office__address">Unit 1407, K18 18 Tai Lok Shan<br>Road, Hong Kong</p>
    </address>

    <ul class="contacts">
      <li><svg viewBox="0 0 12 12" aria-hidden="true"><path d="M3 0h6a1 1 0 0 1 1 1v10a1 1 0 0 1-1 1H3a1 1 0 0 1-1-1V1a1 1 0 0 1 1-1zm0 2v7h6V2z"/></svg>+852 6038 1742</li>
      <li><svg viewBox="0 0 12 12" aria-hidden="true"><path d="M2.4 0.5l2 2.2-1 1.4c.8 1.7 2.1 3 3.8 3.8l1.4-1 2.2 2-1.2 2.1C4.7 11 1 7.3 0.3 2z"/></svg>+852 2836 4100</li>
      <li><svg viewBox="0 0 12 12" aria-hidden="true"><path d="M3 0h5v3h3a1 1 0 0 1 1 1v7a1 1 0 0 1-1 1H1a1 1 0 0 1-1-1V4a1 1 0 0 1 1-1h2zm1 1v3h3V1zM2 6v1h2V6zm3 0v1h2V6zm3 0v1h2V6zM2 8v1h2V8zm3 0v1h2V8zm3 0v1h2V8z"/></svg>+852 2836 4177</li>
      <li><svg viewBox="0 0 12 12" aria-hidden="true"><path d="M0 2h12v1L6 7 0 3zm0 2.2l6 4 6-4V10H0z"/></svg>cjtsang@orinvantage.com</li>
      <li>VOIP: 4158</li>
    </ul>
  </section>

  <section class="card card--back">
    <div class="back-field" role="img" aria-label="Faint large brand pattern in deep navy tones"></div>
    <p class="back-name">ORIN VANTAGE ASIA PACIFIC</p>
  </section>
</main>
</body>
</html>
```